Business Cards for a law firm

Business cards for our law firm. Use our silhoette logo and OAK PARTNERS - check our website (www.oakpartners.example)

Contact Information for Business Card

our silhouette logo, OAK PARTNERS, 800-555-0147, Dorian Pemberton, dorian@oakpartners.example

Requirements
Must have
• our silhouette logo, OAK PARTNERS, 800-555-0147, Dorian Pemberton, dorian@oakpartners.example

```html
<!DOCTYPE html>
<html lang="en">
<head>
<meta charset="utf-8">
<title>Oak Partners – Business Cards</title>
<link rel="stylesheet" href="https://fonts.googleapis.com/css2?family=Questrial&display=swap">
<style>
  :root {
    --backdrop: #e3e7e8;
    --card-navy: #23336a;
    --brand-blue: #3a78c4;
    --ink-white: #ffffff;
    --font-main: "Questrial", sans-serif;
  }
  * { box-sizing: border-box; margin: 0; padding: 0; }
  html, body {
    width: 1200px; height: 960px; overflow: hidden;
    background: var(--backdrop);
    font-family: var(--font-main);
  }
  .card {
    position: absolute;
    left: 252px;
    width: 699px;
    height: 400px;
    border-radius: 28px;
    background: var(--card-navy);
    overflow: hidden;
  }
  .card--front { top: 60px; }
  .card--back { top: 500px; }

  /* front */
  .front-mark {
    position: absolute;
    left: 150px; top: 170px;
    width: 58px; height: 58px;
    background: var(--brand-blue);
  }
  .front-wordmark {
    position: absolute;
    left: 227px; top: 138px;
    color: var(--brand-blue);
    font-size: 56px;
    line-height: 52px;
    letter-spacing: 1px;
  }

  /* back */
  .side-wordmark {
    position: absolute;
    left: 52px; top: 23px;
    transform-origin: 0 0;
    transform: translate(-18px, 296px) rotate(-90deg);
    color: var(--ink-white);
    font-size: 35px;
    line-height: 36px;
    letter-spacing: 1px;
    white-space: nowrap;
  }
  .side-mark {
    position: absolute;
    left: 40px; top: 334px;
    width: 36px; height: 36px;
    background: var(--ink-white);
  }
  .holder-name {
    position: absolute;
    right: 29px; top: 210px;
    color: var(--ink-white);
    font-size: 28px;
    font-variant: small-caps;
    letter-spacing: 1.5px;
    white-space: nowrap;
  }
  .contact-list {
    position: absolute;
    right: 28px; top: 298px;
    list-style: none;
    color: var(--ink-white);
    font-size: 18px;
    letter-spacing: 0.8px;
  }
  .contact-list li {
    display: flex;
    justify-content: flex-end;
    align-items: center;
    gap: 12px;
    height: 23px;
  }
  .contact-list svg { width: 16px; height: 16px; flex: none; }
</style>
</head>
<body>
  <section class="card card--front" aria-label="Card front">
    <div class="front-mark"></div>
    <div class="front-wordmark">OAK<br>PARTNERS</div>
  </section>

  <section class="card card--back" aria-label="Card back">
    <div class="side-wordmark">OAK PARTNERS</div>
    <div class="side-mark"></div>
    <div class="holder-name">Dorian Pemberton</div>
    <ul class="contact-list">
      <li>800-555-0147
        <svg viewBox="0 0 16 16" aria-hidden="true"><path fill="#fff" d="M3.5 1.5l2.3 2.6-1.2 1.6c.9 2 2.6 3.7 4.6 4.6l1.6-1.2 2.6 2.3-1.4 2.2C7.4 13.4 2.6 8.6 2.4 3z"/></svg>
      </li>
      <li>WWW.OAKPARTNERS.EXAMPLE
        <svg viewBox="0 0 16 16" aria-hidden="true"><circle cx="8" cy="8" r="6.5" fill="none" stroke="#fff" stroke-width="1.4"/><path d="M1.5 8h13M8 1.5c-2.5 3-2.5 10 0 13M8 1.5c2.5 3 2.5 10 0 13" fill="none" stroke="#fff" stroke-width="1.1"/></svg>
      </li>
      <li>DORIAN@OAKPARTNERS.EXAMPLE
        <svg viewBox="0 0 16 16" aria-hidden="true"><rect x="1.5" y="3.5" width="13" height="9.5" fill="none" stroke="#fff" stroke-width="1.4"/><path d="M1.5 4l6.5 5 6.5-5" fill="none" stroke="#fff" stroke-width="1.4"/></svg>
      </li>
    </ul>
  </section>
</body>
</html>
```